Generate website for parcelnook.com

Please design a website for our business. It must be clean, streamlined and obvious.

Our business combines ecommerce, with social networking, and zorvi maps. The logo is a shopping bag (ecommerce) and honeycombs inside representing the various compartments of business that are offered throughout site.

Clients use our site to visit the interior of stores and restaurants through video streaming and can virtually "walk through" the store and purchase items with friends and loved ones through the web.

We want to incorporate this logo with the work that we are doing and play on this honeycomb theme.

Our business is "parcelnook.com" because we are all about "u"!

Please make homepage with about us tab, contact us form, mission tab, we also want a page with our research links included that bolster the case for our startup.

We will incorporate a small video on the front screen. A homepage like fildrawer.com only this time with our parcelnook!

Also include, COMING SOON, on the homepage please.
Updates

These are some good templates/example sites of clean and simple but effective: https://7elmrow.com/preview www.fildrawer.com

We are excited to see your submissions. Currently, a very good and only one designer has posted so far. Let us know!

Please include the TM (trademark) symbol after the logo, the name, and the slogan throughout the website. Thank you!

Put the TM after the LOGO and after the slogan "Placement ran Supreme" Lorcan

Target Market(s)

We will begin with female online shoppers.

Industry/Entity Type

Shopping

Font styles to use
Serif
Sans Serif

Colors
e567a6
fece3e
85cae6

Requirements
Must have
• Clean Look
Simple like Fildrawer with simple options "see film" or login/signup.

With browser tabs at the bottom much like fildrawer.

1. Shopper when opening Parcelnook.com website will see a simple webpage with a large Parcelnook logo in the center.

2. User will see log-in and password or create account in upper right hand corner of webpage. Mobile device website will be underneath logo.

3.We Prefer a background for webpages adding a softer experience on the the eyes of the user. A photo in the background to show shopretail experience.

4. Clicking on theParcelnook logo will inform users of details and instructions about platform. Example: About, contact, mission, Help etc. Logo will become somewhat like an interactive tool for help and guidance.

5. Parcelnook is currently scouting for it's founding venues. A founding venue will be the first venues to appear to the public on the Parcelnook platform. Founding venues (FV) will inherit a lifetime of the lowest possible rates of 2%* for the duration of it's business. All businesses wishing to participate in the founding venues offer please leave your email address and store name and a representative will get back with you.

*Venues will be subjected to credit card and CoinTrail rates in addition.

Nice to have
• http://www.zorvi.com/patents/US5193774

Must include the link above/visual of this page on the site as well.

```html
<!DOCTYPE html>
<html lang="en">
<head>
<meta charset="utf-8">
<title>Parcelnook — Shop and walk with friends through the aisles</title>
<link rel="stylesheet" href="https://fonts.googleapis.com/css2?family=Questrial&family=Jost:wght@400&display=swap">
<style>
  :root {
    --ink: #000000;
    --paper: #ffffff;
    --logo-grey: #5a5a5a;
    --tag-ink: #1a1a1a;
    --band: rgba(255,255,255,0.55);
    --button-top: #ff9a86;
    --button-bottom: #f0604c;
    --rule: #6b6b6b;
    --store-warm: #b69a7c;
    --store-mid: #8c7761;
    --store-dark: #4a3b30;
    --logo-mark: #9b59b6;
  }
  * { margin: 0; padding: 0; box-sizing: border-box; }
  html, body { width: 1200px; height: 1091px; overflow: hidden; background: var(--ink); }
  .page { position: relative; width: 1200px; height: 1091px; font-family: Arial, Helvetica, sans-serif; }

  .top-nav { position: absolute; left: 0; top: 0; width: 1200px; height: 136px; background: var(--ink); }
  .top-nav a {
    position: absolute; top: 56px; transform: translateX(-50%);
    color: var(--paper); text-decoration: none; font-size: 21px;
  }

  .store-backdrop {
    position: absolute; left: 0; top: 136px; width: 1200px; height: 826px;
    background:
      radial-gradient(ellipse at 50% 10%, #d8cdbf 0%, transparent 55%),
      linear-gradient(180deg, var(--store-warm) 0%, var(--store-mid) 55%, var(--store-dark) 100%);
  }

  .hero-band { position: absolute; left: 0; top: 255px; width: 1200px; height: 516px; background: var(--band); }

  .brand { position: absolute; left: 330px; top: 292px; display: flex; align-items: center; }
  .brand-mark { width: 110px; height: 110px; background: var(--logo-mark); border-radius: 8px; margin-right: 26px; }
  .brand-name { font-family: "Questrial", sans-serif; font-size: 72px; color: var(--logo-grey); font-weight: 400; line-height: 1; }

  .tagline {
    position: absolute; left: 0; width: 1182px; top: 444px; text-align: center;
    font-family: "Questrial", sans-serif; font-size: 25px; color: var(--tag-ink);
  }

  .signup-col { position: absolute; top: 500px; width: 420px; text-align: center; }
  .signup-col h2 {
    font-family: "Jost", sans-serif; font-weight: 400; font-size: 35px; line-height: 52px;
    color: var(--paper); text-shadow: 0 2px 5px rgba(0,0,0,0.55);
  }
  .col-shoppers { left: 166px; }
  .col-stores { left: 644px; }

  .divider { position: absolute; left: 616px; top: 505px; width: 2px; height: 242px; background: var(--paper); }

  .enroll-box {
    position: absolute; top: 611px; width: 380px; height: 142px;
    border: 2px solid var(--paper); border-radius: 12px; text-align: center;
  }
  .box-shoppers { left: 188px; }
  .box-stores { left: 659px; }
  .enroll-box p {
    margin-top: 8px; font-family: "Jost", sans-serif; font-size: 28px;
    color: var(--paper); text-shadow: 0 2px 4px rgba(0,0,0,0.5);
  }
  .email-field {
    position: absolute; left: 61px; top: 50px; width: 252px; height: 66px;
    background: linear-gradient(180deg, var(--button-top), var(--button-bottom));
    border: 2px solid var(--paper); box-shadow: 0 3px 6px rgba(0,0,0,0.45);
    color: var(--paper); font-family: "Jost", sans-serif; font-size: 22px;
    line-height: 60px; text-align: left; padding-left: 14px;
    text-shadow: 0 1px 3px rgba(0,0,0,0.4);
  }

  .site-footer { position: absolute; left: 0; top: 962px; width: 1200px; height: 129px; background: var(--ink); color: var(--paper); text-align: center; }
  .offer { position: absolute; left: 0; width: 1200px; font-size: 20px; }
  .offer-fee { top: 8px; }
  .offer-limit { top: 40px; }
  .footer-rule { position: absolute; left: 63px; top: 75px; width: 1096px; height: 1px; background: var(--rule); }
  .legal { position: absolute; left: 0; width: 1200px; top: 86px; font-family: "Questrial", sans-serif; font-size: 14px; }
</style>
</head>
<body>
<div class="page">
  <nav class="top-nav">
    <a href="#about" style="left:175px">About us</a>
    <a href="#mission" style="left:425px">Mission</a>
    <a href="#coming-soon" style="left:756px">Coming soon</a>
    <a href="#contact" style="left:1023px">Contact us</a>
  </nav>

  <div class="store-backdrop" role="img" aria-label="Softly blurred photo of a western-wear store interior with clothing racks, hats and boots"></div>

  <section class="hero-band">
  </section>

  <div class="brand">
    <span class="brand-mark"></span>
    <span class="brand-name">Parcelnook</span>
  </div>
  <p class="tagline">Shop and walk with friends through the aisles</p>

  <div class="signup-col col-shoppers"><h2>Sign up to join the<br>experience</h2></div>
  <div class="divider"></div>
  <div class="signup-col col-stores"><h2>Request or Become a<br>participating store</h2></div>

  <div class="enroll-box box-shoppers">
    <p>Enroll here to shop</p>
    <div class="email-field">Enter email adresse</div>
  </div>
  <div class="enroll-box box-stores">
    <p>Enroll or nominate a shop</p>
    <div class="email-field">Enter email adresse</div>
  </div>

  <footer class="site-footer">
    <p class="offer offer-fee">Founding venues will inherit a 2% lifetime fee*</p>
    <p class="offer offer-limit">Limited to a select few</p>
    <div class="footer-rule"></div>
    <p class="legal">©2014 · Parcelnook.com LLC. All rights reserved. Under authorized use of patent #5193774 Patreg</p>
  </footer>
</div>
</body>
</html>
```